Design a business card
Business name: Harbourline Growth Advisory
Improving Business Profitibility

- An Overview of the Business & Service:

Business Performance Consulting

- The Target Market: Small to medium-sized business

- Design Specifics:
White card, blue ink, moon eclipse

No Logo

Target Market(s)

Small to medium-sized business

Font styles to use
Sans Serif

```html
<!DOCTYPE html>
<html lang="en">
<head>
<meta charset="utf-8">
<title>Harbourline Growth Advisory – Business Card</title>
<link rel="stylesheet" href="https://fonts.googleapis.com/css2?family=Jost:ital,wght@0,400;0,500;0,600;1,500&display=swap">
<style>
  :root {
    --bg: #2a2c30;
    --blue: #1f74c4;
    --blue-light: #3592d8;
    --blue-dark: #1763ad;
    --grey-band: #e4e6e9;
    --white: #ffffff;
    --ink: #1f6fc0;
  }
  * { box-sizing: border-box; margin: 0; padding: 0; }
  html, body { width: 1200px; height: 900px; overflow: hidden; }
  body {
    background: var(--bg);
    font-family: "Jost", sans-serif;
    display: flex;
    align-items: center;
    justify-content: center;
    gap: 40px;
  }
  .card {
    width: 540px;
    height: 309px;
    border-radius: 20px;
    overflow: hidden;
    position: relative;
  }

  /* Front */
  .card--front { background: var(--white); display: flex; flex-direction: column; }
  .front__title-band {
    height: 46px;
    background: var(--blue);
    color: var(--white);
    font-weight: 600;
    font-size: 22px;
    display: flex; align-items: center; justify-content: flex-end;
    padding: 0 30px;
    letter-spacing: 0.2px;
  }
  .front__tagline-band {
    height: 24px;
    background: var(--grey-band);
    color: var(--ink);
    font-style: italic;
    font-weight: 500;
    font-size: 14px;
    display: flex; align-items: center; justify-content: flex-end;
    padding: 0 34px;
  }
  .front__body {
    flex: 1;
    display: flex;
    justify-content: space-between;
    align-items: flex-start;
    padding: 26px 30px 0 34px;
  }
  .person__name { color: var(--ink); font-weight: 600; font-size: 23px; line-height: 1.1; }
  .person__role { color: var(--ink); font-size: 11px; letter-spacing: 0.6px; margin-top: 3px; }
  .contact { list-style: none; margin-top: 28px; }
  .contact__item {
    display: flex; align-items: center; gap: 12px;
    color: var(--ink); font-size: 15px; line-height: 1; margin-bottom: 9px;
  }
  .contact__icon { width: 16px; height: 16px; flex: none; fill: var(--ink); }
  .front__footer-band {
    height: 64px;
    background: var(--blue);
    color: var(--white);
    display: flex; align-items: center; gap: 18px;
    padding: 0 26px;
    font-size: 17px;
    font-weight: 500;
    white-space: nowrap;
  }
  .front__footer-rule { flex: 1; height: 2px; background: var(--white); }

  /* Back */
  .card--back {
    background: linear-gradient(160deg, var(--blue-dark) 0%, var(--blue) 45%, var(--blue-light) 100%);
    display: flex; align-items: center; justify-content: center;
  }
  .back__name {
    color: var(--white);
    font-weight: 600;
    font-size: 34px;
    line-height: 1.15;
    text-align: center;
  }
</style>
</head>
<body>
  <section class="card card--front" aria-label="Business card front">
    <header class="front__title-band">Harbourline Growth Advisory</header>
    <div class="front__tagline-band">Improving Business Profitibility</div>
    <div class="front__body">
      <div class="person">
        <p class="person__name">Desmond R Akerly</p>
        <p class="person__role">DIRECTOR</p>
      </div>
      <ul class="contact">
        <li class="contact__item">
          <svg class="contact__icon" viewBox="0 0 16 16" aria-hidden="true"><path d="M3.5 1.5l2.5 0 1 3.2-1.6 1.2a9 9 0 0 0 4.7 4.7l1.2-1.6 3.2 1v2.5c0 .8-.7 1.5-1.5 1.5C6.8 14 2 9.2 2 3c0-.8.7-1.5 1.5-1.5z"/></svg>
          <span>123 456 789</span>
        </li>
        <li class="contact__item">
          <svg class="contact__icon" viewBox="0 0 16 16" aria-hidden="true"><path d="M1 3.5h14v9H1z M1.6 4l6.4 5 6.4-5" fill="none" stroke="#1f6fc0" stroke-width="1.4"/><path d="M1 3.5h14L8 9z"/></svg>
          <span>email@domainname.com</span>
        </li>
        <li class="contact__item">
          <svg class="contact__icon" viewBox="0 0 16 16" aria-hidden="true"><g fill="none" stroke="#1f6fc0" stroke-width="1.3"><circle cx="8" cy="8" r="6.5"/><ellipse cx="8" cy="8" rx="3" ry="6.5"/><path d="M1.5 8h13M2.6 4.6h10.8M2.6 11.4h10.8"/></g></svg>
          <span>www.websiteaddress.com</span>
        </li>
      </ul>
    </div>
    <footer class="front__footer-band">
      <span class="front__footer-rule"></span>
      <span>Business Performance Consulting</span>
      <span class="front__footer-rule"></span>
    </footer>
  </section>

  <section class="card card--back" aria-label="Business card back">
    <p class="back__name">Harbourline<br>Growth Advisory</p>
  </section>
</body>
</html>
```